Shopping center investment profile

We need to design a two-page 8.5" x 11" brochure that can be used as a template for profiling our shopping centers and demonstrating our track record to investors.

Our company (QLM Real Estate Investments) owns retail shopping centers in the southwestern United States. Our website is www.qlmvx.example, but we will be redesigning and modernizing the website and logo in the near future, so please do not use the color schemes or framework of the website for the brochure.

Our investors are institutional and high net worth investors who typically have an existing relationship with our company. They are determining whether to invest multi-millions of dollars in a shopping center opportunity, so the brochure needs to be professional, very high quality and provide key information about the specific property.
Updates

Additional guidance on color scheme:

We would like to see a Blue (something like Hex #5A61BC) and Gold (Hex #EDB215) or (Hex #DDA24B) color scheme with some Black accents 

Thank you!

Target Market(s)

Our target audiences are institutional investors, high net-worth individuals, financial firms and medium to large commercial real estate companies.

Industry/Entity Type

Investment

Requirements
Must have
• Clean and modern look with corresponding fonts and colors.
• Incorporates the information found in the attached "Harborline Commons profile" Pages or PDF file.
• Final file design files that can be modified easily
Nice to have
• Two examples of industry brochures are attached. These are examples of the professional quality that we are looking for, not necessarily the design or format.

```html
<!DOCTYPE html>
<html lang="en">
<head>
<meta charset="utf-8">
<title>Harborline Commons – Property Profile</title>
<link rel="stylesheet" href="https://fonts.googleapis.com/css2?family=Open+Sans:wght@700&family=Raleway:wght@400;500&family=Dosis:wght@500;600&family=Barlow+Semi+Condensed:wght@500&display=swap">
<style>
:root{
  --blue:#4b78b2;
  --blue-deep:#2d64a4;
  --navy:#1f5a9a;
  --grey:#9b9b9b;
  --text:#4a4a4a;
  --paper:#f7f7f8;
  --rule:#a9c0dc;
}
*{margin:0;padding:0;box-sizing:border-box}
html,body{width:887px;height:1200px;overflow:hidden;background:var(--paper)}
.sheet{position:relative;width:887px;height:1200px;background:var(--paper);font-family:"Raleway",sans-serif;color:var(--text)}
.abs{position:absolute;z-index:2}
.shape{position:absolute;left:0;top:0;z-index:1}
.address{left:60px;top:58px;font-family:"Barlow Semi Condensed",sans-serif;font-weight:500;font-size:24px;line-height:28px;color:#fff;letter-spacing:.5px}
.title{right:55px;top:42px;text-align:right;font-family:"Open Sans",sans-serif;font-weight:700;line-height:1.2}
.title .name{font-size:33px;color:var(--navy)}
.title .sub{font-size:38px;color:var(--grey)}
.section-head{font-family:"Dosis",sans-serif;font-weight:600;font-size:21px;line-height:25px;color:var(--navy)}
.opportunity{left:37px;top:152px;width:373px}
.opportunity .section-head{border-bottom:1.5px solid var(--blue);padding-bottom:3px}
.opportunity ul{list-style:none;margin-top:12px}
.opportunity li{position:relative;padding-left:19px;font-size:13.4px;line-height:15.5px;margin-bottom:15.5px;text-align:justify}
.opportunity li::before{content:"";position:absolute;left:4px;top:4px;width:7px;height:7px;border-radius:50%;background:#8d8fb8}
.tab{font-family:"Dosis",sans-serif;font-weight:600;color:#fff;font-size:21px}
.table{font-family:"Dosis",sans-serif;font-weight:500;color:#fff;font-size:14.5px}
.row{position:absolute;z-index:2;display:flex;justify-content:space-between;align-items:center;border-bottom:1.5px solid var(--rule);height:28px}
.summary .row{left:459px;width:374px;padding:0 11px}
.invest .row{left:73px;width:367px;padding:0 11px;height:31px}
.total{left:85px;top:1026px;width:334px;height:37px;background:var(--blue-deep);color:#fff;font-family:"Dosis",sans-serif;font-weight:500;font-size:15px;line-height:37px;padding:0 18px}
.structure{left:73px;top:1110px;width:367px;display:flex;justify-content:space-between;padding:0 11px;font-family:"Dosis",sans-serif;font-weight:500;color:#fff;font-size:14.5px}
.structure ul{list-style:none;line-height:16px;width:150px}
.structure li::before{content:"• "}
.hero{position:absolute;z-index:0;left:109px;top:484px;width:669px;height:356px;background:linear-gradient(180deg,#5fa2dc 0%,#b9d6ee 40%,#c9875f 62%,#b5563f 75%,#55575c 100%);clip-path:polygon(0 0,94% 0,100% 12%,100% 100%,0 100%)}
.results{left:507px;top:875px;width:341px}
.results .section-head{border-bottom:1.5px solid var(--blue);padding-bottom:3px}
.results ul{list-style:none;margin-top:12px}
.results li{position:relative;padding-left:25px;font-size:13.4px;line-height:15.5px;margin-bottom:15.5px;text-align:justify}
.results li svg{position:absolute;left:0;top:2px}
.web{left:622px;top:1154px;font-size:17px;line-height:20px;letter-spacing:3.5px;color:var(--navy);display:flex;align-items:center;gap:6px}
</style>
</head>
<body>
<div class="sheet">
  <div class="hero" role="img" aria-label="Architectural rendering of the shopping center storefronts with trees and parked cars"></div>

  <svg class="shape" width="887" height="1200" viewBox="0 0 887 1200" aria-hidden="true">
    <defs>
      <linearGradient id="steel" x1="0" x2="1"><stop offset="0" stop-color="#8d8d8d"/><stop offset=".5" stop-color="#d4d4d4"/><stop offset="1" stop-color="#8d8d8d"/></linearGradient>
    </defs>
    <rect x="233" y="32" width="242" height="4" fill="url(#steel)"/>
    <polygon points="0,45 463,45 433,123 0,123" fill="var(--blue)"/>
    <rect x="18" y="129" width="251" height="4" fill="url(#steel)"/>
    <polygon points="442,163 570,163 578,173 578,205 442,205" fill="var(--blue-deep)"/>
    <polygon points="442,206 822,206 845,230 845,452 470,452 442,426" fill="var(--blue)"/>
    <polygon points="47,812 313,812 321,822 321,853 47,853" fill="var(--blue-deep)"/>
    <polygon points="45,857 445,857 468,880 468,1161 70,1161 45,1136" fill="var(--blue)"/>
    <polygon points="590,1127 887,1127 887,1139 600,1139 580,1172 560,1172" fill="url(#steel)"/>
    <rect x="0" y="1173" width="887" height="5" fill="url(#steel)"/>
  </svg>

  <div class="abs address">SWC OF HARBOR RD AND<br>MERIDIAN RD CALDER, ARIZONA</div>
  <div class="abs title"><div class="name">Harborline Commons</div><div class="sub">Property Profile</div></div>

  <section class="abs opportunity">
    <h2 class="section-head">Opportunity</h2>
    <ul>
      <li>Bank owned property with attractive purchase price</li>
      <li>Strong relationship with seller's broker and decision makers</li>
      <li>Redevelopment upside with management and leasing</li>
      <li>No major renovations required</li>
      <li>Calder location has very strong population, education and income demographics</li>
      <li>Adjacent to premier 2,500-residence master planned community of Willow Crest Lakes</li>
      <li>Strong employment area with the new Northgate Regional hospital and the adjacent Linwood Cancer center</li>
    </ul>
  </section>

  <div class="abs tab" style="left:461px;top:170px">Summary</div>
  <div class="summary table">
    <div class="row" style="top:228px"><span>Property Type</span><span>Shopping Center</span></div>
    <div class="row" style="top:256px"><span>Size</span><span>79,490 sq ft</span></div>
    <div class="row" style="top:284px"><span>Purchased</span><span>April 2011</span></div>
    <div class="row" style="top:312px"><span>Total Investment</span><span>$X,XXX,XXX</span></div>
    <div class="row" style="top:341px"><span>Purchase Occupancy</span><span>8.39%</span></div>
    <div class="row" style="top:369px"><span>Current Occupancy</span><span>97.29%</span></div>
    <div class="row" style="top:398px;border-bottom:none"><span>Projected 5-year IRR (Unleveraged)</span><span>XX.XX%</span></div>
  </div>

  <div class="abs tab" style="left:66px;top:819px">Investment Information</div>
  <div class="invest table">
    <div class="row" style="top:869px"><span>Purchase Price</span><span>$X,XXX,XXX</span></div>
    <div class="row" style="top:900px"><span>Sponsor Acquisition Fee</span><span>$XX,XXX</span></div>
    <div class="row" style="top:931px"><span>Painting and Landscape</span><span>$XXX,XXX</span></div>
    <div class="row" style="top:962px"><span>TI/LC Reserve</span><span>$X,XXX,XXX</span></div>
    <div class="row" style="top:993px;border-bottom:none"><span>Operating Expenses</span><span>$XXX,XXX</span></div>
    <div class="row" style="top:1066px;height:31px;border-top:1.5px solid var(--rule)"><span>Investor / Sponsor Split</span><span>XX% / XX%</span></div>
  </div>
  <div class="abs total">Total Cash Investment</div>
  <div class="abs structure">
    <span>Structure</span>
    <ul><li>Cash Flow Pari Passu</li><li>Acquisition Fee</li><li>Management Fee</li></ul>
  </div>

  <section class="abs results">
    <h2 class="section-head">Results</h2>
    <ul>
      <li><svg width="18" height="16" viewBox="0 0 18 16" aria-hidden="true"><rect x="1" y="3" width="12" height="12" fill="none" stroke="var(--blue-deep)" stroke-width="1.6"/><path d="M4 8l3 4 9-11" fill="none" stroke="var(--blue-deep)" stroke-width="2.2"/></svg>Stabilized the shopping center within three years, producing excellent results for investors</li>
      <li><svg width="18" height="16" viewBox="0 0 18 16" aria-hidden="true"><rect x="1" y="3" width="12" height="12" fill="none" stroke="var(--blue-deep)" stroke-width="1.6"/><path d="M4 8l3 4 9-11" fill="none" stroke="var(--blue-deep)" stroke-width="2.2"/></svg>Transformed the center into a vibrant destination that the surrounding community is excited about</li>
      <li><svg width="18" height="16" viewBox="0 0 18 16" aria-hidden="true"><rect x="1" y="3" width="12" height="12" fill="none" stroke="var(--blue-deep)" stroke-width="1.6"/><path d="M4 8l3 4 9-11" fill="none" stroke="var(--blue-deep)" stroke-width="2.2"/></svg>Transitioned legacy tenants to upgrade the business operators</li>
      <li><svg width="18" height="16" viewBox="0 0 18 16" aria-hidden="true"><rect x="1" y="3" width="12" height="12" fill="none" stroke="var(--blue-deep)" stroke-width="1.6"/><path d="M4 8l3 4 9-11" fill="none" stroke="var(--blue-deep)" stroke-width="2.2"/></svg>Reduced the shopping center's operating expenses by replacing vendors and appealing property taxes</li>
    </ul>
  </section>

  <div class="abs web"><svg width="13" height="13" viewBox="0 0 14 14" aria-hidden="true"><circle cx="7" cy="7" r="6" fill="none" stroke="var(--navy)" stroke-width="1.2"/><ellipse cx="7" cy="7" rx="2.6" ry="6" fill="none" stroke="var(--navy)" stroke-width="1"/><path d="M1 7h12" stroke="var(--navy)" stroke-width="1"/></svg>www.qlmvx.example</div>
</div>
</body>
</html>
```